Black Car Limousine transportation business in Naples Florida

Always stand for my reliability and RVD stands for Love, K and M are the first initials of my children's names. It should show professionalism and a dedication to customer service. We keep our clients identities private. Show our professionalism. We are Black car Black tie company. We service transportation on a reserve basis to and from residents, airports, casinos, hotels,

Target Market(s)

It is a Private car service. High end clients. Businesses, Celebrity and athletes. Service to airports, hotels, special events.

Industry/Entity Type

Business

Contact Information for Business Card

A pearl metallic or Luster card. Standard business card size. Would like the name, Company email, show we take credit cards and phone number. Currently I don't have a website but will like to add later.

Logo Text

STEADFAST RVD TRANSPORTATION

Font styles to use
Serif

Colors
eaeaea
000000

Requirements
Must have
• Must have Company email, show we take credit cards and phone number. Currently I don't have a website but will like to add later.
Nice to have
• Would like to stay with a black and white theme. Open to some color trim.
Should not have
• Open to suggestions

```html
<!DOCTYPE html>
<html lang="en">
<head>
<meta charset="utf-8">
<title>Steadfast RVD Transportation – Business Card</title>
<link rel="stylesheet" href="https://fonts.googleapis.com/css2?family=Open+Sans:wght@400;600;700&family=Source+Serif+4:wght@400;600;700&display=swap">
<style>
  :root {
    --page: #e6e4e0;
    --card-dark: #333333;
    --card-band: #4d4d4d;
    --card-light: #ffffff;
    --ink-dark: #2b2b2b;
    --ink-light: #ffffff;
    --ink-soft: #d9d9d9;
    --vehicle-top: #3a3a3a;
    --vehicle-bottom: #0d0d0d;
  }
  * { box-sizing: border-box; margin: 0; padding: 0; }
  html, body {
    width: 1200px; height: 900px; overflow: hidden;
    background: var(--page);
    font-family: "Open Sans", Arial, sans-serif;
  }
  .sheet {
    position: relative; width: 1200px; height: 900px;
    display: flex; flex-direction: column; align-items: center; justify-content: center; gap: 46px;
  }
  .card {
    position: relative; width: 660px; height: 377px; overflow: hidden;
    box-shadow: 0 6px 18px rgba(0,0,0,0.18);
  }

  /* Logo lockup */
  .brand {
    display: flex; align-items: center; gap: 12px;
    font-family: "Source Serif 4", Georgia, serif; font-weight: 700; line-height: 1;
    white-space: nowrap;
  }
  .brand__square { width: 20px; height: 20px; background: currentColor; flex: none; }
  .brand__name { display: flex; flex-direction: column; gap: 6px; }
  .brand__main { font-size: 32px; letter-spacing: 0.5px; }
  .brand__sub { font-size: 19px; letter-spacing: 2px; }

  /* Back card */
  .card--back { background: var(--card-dark); }
  .card--back .band {
    position: absolute; left: 0; right: 0; top: 228px; bottom: 0;
    background: var(--card-band);
  }
  .card--back .brand { position: absolute; left: 58px; top: 104px; color: var(--ink-soft); }
  .card--back .vehicle {
    position: absolute; left: 400px; top: 104px; width: 236px; height: 180px;
    border-radius: 28px 42px 16px 16px;
    background: linear-gradient(180deg, var(--vehicle-top), var(--vehicle-bottom));
  }
  .card--back .web {
    position: absolute; left: 58px; bottom: 52px;
    color: var(--ink-light); font-size: 17px; font-weight: 600; letter-spacing: 0.3px;
  }

  /* Front card */
  .card--front { background: var(--card-light); }
  .card--front .band {
    position: absolute; left: 0; right: 0; top: 200px; bottom: 0;
    background: var(--card-dark);
  }
  .card--front .brand { position: absolute; left: 200px; top: 66px; color: var(--ink-dark); }
  .card--front .brand__main { font-size: 44px; }
  .card--front .brand__sub { font-size: 24px; }

  .contact {
    position: absolute; left: 0; right: 0; top: 220px;
    display: flex; justify-content: center; align-items: stretch; gap: 18px;
    color: var(--ink-light);
  }
  .person { text-align: right; padding-top: 24px; }
  .person__name { font-family: "Source Serif 4", Georgia, serif; font-size: 20px; font-weight: 700; }
  .person__title { font-size: 15px; margin-top: 2px; }
  .divider { width: 1px; background: var(--ink-light); }
  .details { list-style: none; font-size: 14px; display: flex; flex-direction: column; gap: 5px; }
  .details li { display: flex; align-items: center; gap: 8px; }
  .details svg { width: 13px; height: 13px; fill: var(--ink-light); flex: none; }
  .payments { display: flex; gap: 6px; margin-top: 2px; }
  .payments span { width: 26px; height: 16px; border-radius: 3px; background: var(--ink-soft); }
  .address {
    position: absolute; left: 0; right: 0; bottom: 22px; text-align: center;
    color: var(--ink-light); font-size: 16px;
  }
</style>
</head>
<body>
<main class="sheet">

  <section class="card card--back">
    <div class="band"></div>
    <div class="brand">
      <span class="brand__square"></span>
      <span class="brand__name">
        <span class="brand__main">STEADFAST RVD</span>
        <span class="brand__sub">TRANSPORTATION</span>
      </span>
    </div>
    <div class="vehicle" role="img" aria-label="Photo of a black luxury SUV"></div>
    <p class="web">www.steadfastrvd.com</p>
  </section>

  <section class="card card--front">
    <div class="band"></div>
    <div class="brand">
      <span class="brand__square"></span>
      <span class="brand__name">
        <span class="brand__main">STEADFAST RVD</span>
        <span class="brand__sub">TRANSPORTATION</span>
      </span>
    </div>
    <div class="contact">
      <div class="person">
        <p class="person__name">Marcus Delane</p>
        <p class="person__title">Managing Director</p>
      </div>
      <span class="divider"></span>
      <ul class="details">
        <li>
          <svg viewBox="0 0 24 24" aria-hidden="true"><path d="M6.6 10.8a15.1 15.1 0 0 0 6.6 6.6l2.2-2.2a1 1 0 0 1 1-.25 11.4 11.4 0 0 0 3.6.57 1 1 0 0 1 1 1V20a1 1 0 0 1-1 1A17 17 0 0 1 3 4a1 1 0 0 1 1-1h3.5a1 1 0 0 1 1 1c0 1.25.2 2.45.57 3.57a1 1 0 0 1-.25 1z"/></svg>
          (239)555-0148
        </li>
        <li>
          <svg viewBox="0 0 24 24" aria-hidden="true"><path d="M2 5h20v14H2z M2 5l10 8 10-8" fill="none" stroke="#fff" stroke-width="2"/></svg>
          rides@steadfastrvd.com
        </li>
        <li>
          <svg viewBox="0 0 24 24" aria-hidden="true"><circle cx="12" cy="12" r="10"/></svg>
          www.steadfastrvd.com
        </li>
        <li class="payments" aria-label="Credit cards accepted">
          <span></span><span></span><span></span>
        </li>
      </ul>
    </div>
    <p class="address">4180 Harbor Point Dr, Naples FL, 34102</p>
  </section>

</main>
</body>
</html>
```